Reliable and clean label for a natural product!

We would like to have a label design for our CBD SOFT GEL CAPSULES . We are a business family and believe in the power of natural healing. In this label we would like to show a reliable, natural and feminine product mainly.

Font styles to use
Serif
Sans Serif

Colors

Designer to choose colors to be used in the design.

```html
<!DOCTYPE html>
<html lang="en">
<head>
<meta charset="UTF-8">
<title>Aveline CBD – Soft Gel Capsules Label</title>
<link href="https://fonts.googleapis.com/css2?family=Bebas+Neue&family=Montserrat:wght@400;500;600&display=swap" rel="stylesheet">
<style>
  :root {
    --canvas: #ffffff;
    --label-light: #efe9e0;
    --label-dark: #d5cbbe;
    --bronze-dark: #8a6446;
    --bronze-mid: #b48c6c;
    --bronze-light: #e6d2bf;
    --ink: #262626;
    --ink-soft: #3c3a38;
    --cream-text: #f6eee6;
  }
  html, body {
    margin: 0;
    padding: 0;
    width: 1200px;
    height: 1200px;
    overflow: hidden;
    background: var(--canvas);
  }
  .canvas {
    position: relative;
    width: 1200px;
    height: 1200px;
    background: var(--canvas);
  }
  .label {
    position: absolute;
    left: 240px;
    top: 172px;
    width: 720px;
    height: 856px;
    background: linear-gradient(160deg, var(--label-light) 0%, #e4ddd2 55%, var(--label-dark) 100%);
    font-family: "Montserrat", sans-serif;
    overflow: hidden;
  }
  .side-band {
    position: absolute;
    left: 90px;
    top: 0;
    width: 46px;
    height: 100%;
    background: linear-gradient(180deg, var(--bronze-dark) 0%, var(--bronze-light) 30%, var(--bronze-mid) 60%, var(--bronze-dark) 100%);
  }
  .side-band__text {
    position: absolute;
    left: 50%;
    top: 470px;
    transform: translate(-50%, -50%) rotate(-90deg);
    white-space: nowrap;
    font-size: 33px;
    font-weight: 400;
    letter-spacing: 3px;
    color: var(--cream-text);
  }
  .brand-mark {
    position: absolute;
    left: 282px;
    top: 43px;
    width: 166px;
    height: 166px;
  }
  .brand-name {
    position: absolute;
    left: 190px;
    top: 244px;
    width: 352px;
    text-align: center;
    font-size: 45px;
    font-weight: 500;
    letter-spacing: 1px;
    color: var(--bronze-mid);
    white-space: nowrap;
  }
  .product-title {
    position: absolute;
    left: 192px;
    top: 444px;
    margin: 0;
    font-family: "Bebas Neue", "Oswald", sans-serif;
    font-weight: 400;
    font-size: 106px;
    line-height: 1;
    color: var(--ink);
    letter-spacing: 1px;
    white-space: nowrap;
    -webkit-text-stroke: 1.5px var(--ink);
  }
  .product-type {
    position: absolute;
    left: 196px;
    top: 566px;
    font-size: 50px;
    font-weight: 400;
    color: var(--ink-soft);
    white-space: nowrap;
  }
  .spectrum-tag {
    position: absolute;
    left: 196px;
    top: 661px;
    width: 345px;
    height: 53px;
    background: linear-gradient(90deg, var(--bronze-mid) 0%, var(--bronze-light) 45%, var(--bronze-mid) 75%, var(--bronze-dark) 100%);
    color: var(--cream-text);
    font-size: 31px;
    font-weight: 600;
    letter-spacing: 2px;
    line-height: 53px;
    text-align: center;
    white-space: nowrap;
  }
  .dose {
    position: absolute;
    left: 196px;
    top: 732px;
    font-size: 33px;
    font-weight: 400;
    color: var(--ink-soft);
    white-space: nowrap;
  }
  .count {
    position: absolute;
    left: 196px;
    top: 792px;
    font-size: 30px;
    font-weight: 500;
    color: var(--ink-soft);
    white-space: nowrap;
  }
</style>
</head>
<body>
  <main class="canvas">
    <section class="label">
      <div class="side-band">
        <span class="side-band__text">RESTORATIVE SUPPLEMENT</span>
      </div>

      <svg class="brand-mark" viewBox="0 0 166 166" aria-hidden="true">
        <circle cx="83" cy="83" r="80" fill="none" stroke="#a98163" stroke-width="3"/>
      </svg>
      <div class="brand-name">AVELINE CBD</div>

      <h1 class="product-title">CBD SOFT GELS</h1>
      <div class="product-type">CAPSULES</div>
      <div class="spectrum-tag">FULL SPECTRUM</div>
      <div class="dose">25mg cbd per capsule</div>
      <div class="count">30 CAPSULES</div>
    </section>
  </main>
</body>
</html>
```